Hello my name is Colin, I am Starting a business called Tovira Wellness and fitness and am in need of a memorable business card.
It is a personal training studio. I have added the logo that i would like to be on the left center om my business card. i would like room left up the top for a heading sentence such as. "Is your body shocking for all the wrong reasons". there must be room left on the right of the logo below the main heading for 3 sub headings.
then under those 3 headings and logo room for another larger heading eg. "give me a call and learn how to eat chocolate, drink bear and have great sex". in what room is left i would like to be used for my contact details, use I'm Colin Ferrante your fitness expert on the left then on the right Phone, Email and website space in at least 12 Point. Very specific i know :) now onto the back, for the back i would like an eye catching graphic and room for one main headline and 3 bullet points centered just write anything i will choose what to put in them when i pick a winner. Thank you very much for sticking through all of that :) i appreciate you taking the time to read it and hopefully undergo designing me a business card.
I can't wait to see the designs!

Target Market(s)

slightly more towards females although it would probably be best if it was targeted towards both sexes

Industry/Entity Type

Training

Requirements
Nice to have
• I would love to see if anyone could come up with a design that would really make my card stand out and be memorable.
Should not have
• tacky fitness photos of abs and muscles etc.

```html
<!DOCTYPE html>
<html lang="en">
<head>
<meta charset="utf-8">
<title>Tovira Wellness and fitness – Business Cards</title>
<link href="https://fonts.googleapis.com/css2?family=Jost:wght@400;500;600&display=swap" rel="stylesheet">
<style>
  :root {
    --stage: #6a4331;
    --navy: #1d4a7c;
    --navy-deep: #123966;
    --ink: #3f4246;
    --ink-soft: #5a5d61;
    --ink-dark: #111111;
    --paper: #ffffff;
    --blush-1: #f3e4dc;
    --blush-2: #e6cbbf;
    --ghost: #e9ebf1;
    --ghost-on-navy: rgba(255,255,255,0.13);
  }
  * { margin: 0; padding: 0; box-sizing: border-box; }
  html, body { width: 1200px; height: 745px; overflow: hidden; }
  body {
    background: var(--stage);
    font-family: "Jost", "Futura", sans-serif;
    position: relative;
  }
  .card {
    position: absolute;
    width: 529px;
    height: 302px;
    overflow: hidden;
    box-shadow: 0 2px 6px rgba(0,0,0,0.35);
  }
  .card--front { left: 56px; top: 54px; background: var(--paper); }
  .card--pattern { left: 610px; top: 61px; }
  .card--white { left: 58px; top: 399px; background: var(--paper); }
  .card--navy { left: 622px; top: 405px; background: linear-gradient(180deg, #1f4f85, var(--navy-deep)); }

  /* Front */
  .brand { position: absolute; left: 22px; top: 16px; width: 245px; color: var(--navy); font-weight: 500; line-height: 1; }
  .brand__name { display: block; font-size: 66px; letter-spacing: -1px; }
  .brand__line { display: block; font-size: 19px; margin-top: 6px; text-align: right; }
  .person { position: absolute; left: 20px; top: 122px; }
  .person__name { font-size: 20px; font-weight: 600; color: var(--navy); }
  .person__role { font-size: 15px; color: var(--ink-soft); margin-top: -2px; }
  .contact { position: absolute; left: 20px; top: 174px; list-style: none; }
  .contact li { display: flex; align-items: center; gap: 6px; font-size: 19px; color: var(--ink); height: 27px; }
  .contact svg { width: 16px; height: 16px; flex: none; }
  .divider { position: absolute; left: 288px; top: 22px; width: 1px; height: 236px; background: #c9cbd0; }
  .offer { position: absolute; left: 298px; top: 28px; width: 225px; color: var(--ink-soft); }
  .offer__intro { font-size: 13px; line-height: 16px; }
  .offer__list { list-style: none; margin-top: 22px; font-size: 13px; line-height: 20px; }
  .offer__list li::before {
    content: ""; display: inline-block; width: 4px; height: 4px; border-radius: 50%;
    background: currentColor; margin-right: 6px; vertical-align: middle;
  }
  .offer__pitch { margin-top: 18px; font-size: 16px; font-weight: 600; line-height: 20px; }
  .offer__pitch span { display: block; }
  .offer__pitch .gap { margin-top: 5px; }
  .tagline {
    position: absolute; left: 0; right: 0; bottom: 0; height: 36px;
    border-top: 2px solid var(--navy);
    background: linear-gradient(90deg, var(--navy-deep), #24558c 50%, var(--navy-deep));
    color: #fff; font-size: 18px; font-weight: 600; text-align: center; line-height: 33px;
  }
  .tagline::before { content: ""; position: absolute; left: 0; right: 0; top: -6px; height: 1px; background: var(--navy); }

  /* Backs */
  .pattern-fill {
    position: absolute; inset: 0;
    background: radial-gradient(ellipse at 55% 55%, var(--blush-1), var(--blush-2));
  }
  .ghost-brand { position: absolute; left: 40px; top: 60px; width: 430px; font-weight: 500; line-height: 1; color: var(--ghost); }
  .card--navy .ghost-brand { color: var(--ghost-on-navy); }
  .ghost-brand__name { display: block; font-size: 118px; letter-spacing: -2px; }
  .ghost-brand__line { display: block; font-size: 32px; margin-top: 4px; text-align: right; }
  .back { position: absolute; inset: 0; color: var(--ink); }
  .card--pattern .back { color: var(--ink-dark); }
  .card--navy .back { color: #fff; }
  .back__headline { position: absolute; left: 0; right: 0; top: 82px; text-align: center; font-size: 24px; }
  .back__list { position: absolute; left: 142px; top: 117px; list-style: none; font-size: 25px; line-height: 30px; }
  .back__list li::before {
    content: ""; display: inline-block; width: 10px; height: 10px; border-radius: 50%;
    background: currentColor; margin-right: 10px; vertical-align: middle; position: relative; top: -2px;
  }
  .back__url { position: absolute; left: 0; right: 0; top: 252px; text-align: center; font-size: 20px; font-weight: 500; letter-spacing: 3px; }
</style>
</head>
<body>

<section class="card card--front">
  <div class="brand">
    <span class="brand__name">Tovira</span>
    <span class="brand__line">Wellness and fitness</span>
  </div>
  <div class="person">
    <p class="person__name">Colin Ferrante</p>
    <p class="person__role">Fitness expert</p>
  </div>
  <ul class="contact">
    <li><svg viewBox="0 0 16 16"><circle cx="8" cy="8" r="7" fill="none" stroke="#3f4246" stroke-width="1.4"/><path d="M5.5 4.5c1 0 1.2 1.6.6 2.1.5 1.3 1.4 2.2 2.6 2.8.5-.6 2.1-.4 2.1.6 0 1-1.4 1.5-2.4 1-2-1-3.6-2.6-4.2-4.7-.3-1 .3-1.8 1.3-1.8z" fill="#3f4246"/></svg>0912 348765</li>
    <li><svg viewBox="0 0 16 16"><rect x="1.5" y="5" width="13" height="8.5" rx="1" fill="#3f4246"/><path d="M1.5 6l6.5 4.5L14.5 6" fill="none" stroke="#fff" stroke-width="1.2"/><path d="M3 5l5-3 5 3" fill="none" stroke="#3f4246" stroke-width="1.2"/></svg>info@tovirafit.com</li>
    <li><svg viewBox="0 0 16 16" fill="none" stroke="#3f4246" stroke-width="1.2"><circle cx="8" cy="8" r="6.5"/><ellipse cx="8" cy="8" rx="3" ry="6.5"/><path d="M1.5 8h13M2.5 4.8h11M2.5 11.2h11"/></svg>www.tovirafit.com</li>
  </ul>

  <div class="divider"></div>
  <div class="offer">
    <p class="offer__intro">Lorem ipsum Lorem ipsum<br>Lorem ipsum</p>
    <ul class="offer__list">
      <li>Lorem ipsum diet</li>
      <li>Lorem ipsum diet</li>
      <li>Lorem ipsum diet</li>
    </ul>
    <p class="offer__pitch">
      <span>Give me a call and</span>
      <span>Learn how to eat chocolate drink bear</span>
      <span class="gap">Have great sex</span>
    </p>
  </div>
  <p class="tagline">Is your body shocking for all the wrong reasons</p>
</section>

<section class="card card--pattern">
  <div class="pattern-fill" role="img" aria-label="Decorative swirling floral pattern in soft blush and cream tones"></div>
  <div class="back">
    <p class="back__headline">Lorem Ispum Lorem Ispum Lorem Ispum</p>
    <ul class="back__list">
      <li>Lorem Ispum Lorem</li>
      <li>Lorem Ispum Lorem</li>
      <li>Lorem Ispum Lorem</li>
    </ul>
    <p class="back__url">www.tovirafit.com</p>
  </div>
</section>

<section class="card card--white">
  <div class="ghost-brand" aria-hidden="true">
    <span class="ghost-brand__name">Tovira</span>
    <span class="ghost-brand__line">Wellness and fitness</span>
  </div>
  <div class="back">
    <p class="back__headline">Lorem Ispum Lorem Ispum Lorem Ispum</p>
    <ul class="back__list">
      <li>Lorem Ispum Lorem</li>
      <li>Lorem Ispum Lorem</li>
      <li>Lorem Ispum Lorem</li>
    </ul>
    <p class="back__url">www.tovirafit.com</p>
  </div>
</section>

<section class="card card--navy">
  <div class="ghost-brand" aria-hidden="true">
    <span class="ghost-brand__name">Tovira</span>
    <span class="ghost-brand__line">Wellness and fitness</span>
  </div>
  <div class="back">
    <p class="back__headline">Lorem Ispum Lorem Ispum Lorem Ispum</p>
    <ul class="back__list">
      <li>Lorem Ispum Lorem</li>
      <li>Lorem Ispum Lorem</li>
      <li>Lorem Ispum Lorem</li>
    </ul>
    <p class="back__url">www.tovirafit.com</p>
  </div>
</section>

</body>
</html>
```